Product Description page for Hullwrap.com, References here just need a clean up redesign

Hi, were working on updating the product description page of our site hullwrap.com

Attached is a reference of what we drew on paint. We want to keep it pretty much the same as far as whats on there, the components with a few small adjustments and a clean actually designed look.

1. We want to remove the tabs (product description, warranty, reviews) and put it all in that main content area stretching down into sections. IE: Product Description section, followed by reviews, followed by warranty, below each other.
2. The side bar needs to be redesigned as far as the look and feel but the content and whats in there should stay the same.
3. The main banner area will be replaced shortly you do not have to worry about that.
4. Include a section or box for people to put in their email for a free Ebook.

Target Market(s)

people looking to easily view our boat cover products and buy without having to click too often or leave the page.

Industry/Entity Type

Online Shopping

Number of Pages Required

1 page

Requirements
Must have
• - Must update the sidebar
• - Must update the content area to remove the tabs and put the content from each tab sectioned off below each other (dummy text is fine for now for the tabs you cant view)
Nice to have
• - Cool place thats clean and functional to insert a section for people to put in their email to receive a free ebook
Should not have
• - too much change, we already know what we want and have a solid reference to work from.

```html
<!DOCTYPE html>
<html lang="en">
<head>
<meta charset="utf-8">
<title>Hullwrap.com – Center Console Boat Cover up to 16'8" Long and 90" Wide</title>
<link rel="stylesheet" href="https://fonts.googleapis.com/css2?family=Fira+Sans:wght@400;500;600;700&family=Oswald:wght@500;600&family=Roboto:wght@400;500;700&display=swap">
<style>
:root{
  --brand-blue:#0a3fc2;
  --brand-blue-dark:#0632a0;
  --brand-blue-light:#2f6ae0;
  --link-blue:#1f3fa8;
  --ink:#222222;
  --line:#c9c9c9;
  --soft-line:#dddddd;
  --price-red:#e02020;
  --accent-orange:#f7935c;
  --fits-bg:#f2fcfc;
  --fits-line:#bfe0e0;
  --rating-bg:#e8e8e8;
  --page-bg:#ffffff;
}
*{box-sizing:border-box;margin:0;padding:0}
html,body{width:1200px;height:2817px;overflow:hidden;background:var(--page-bg)}
body{position:relative;font-family:"Fira Sans",Arial,sans-serif;color:var(--ink)}
.abs{position:absolute}

.page-header{left:0;top:0;width:1200px;height:103px;background:linear-gradient(180deg,var(--brand-blue-light),var(--brand-blue) 55%,var(--brand-blue-dark))}
.page-header h1{position:absolute;left:103px;top:30px;font-family:"Oswald",sans-serif;font-weight:600;font-size:34px;color:#fff;letter-spacing:.3px}

.breadcrumb{left:112px;top:137px;font-size:16px;color:#333}
.breadcrumb span{margin-right:8px}
.breadcrumb .current{color:var(--link-blue)}

.product-frame{left:75px;top:186px;width:1040px;height:2318px;border:2px solid var(--line);border-radius:8px}

.fits-bar{left:116px;top:203px;width:972px;height:62px;background:var(--fits-bg);border:1px solid var(--fits-line);font-size:20px;line-height:60px;padding-left:18px;color:#333}

.hero-photo{left:170px;top:282px;width:880px;height:340px;background:linear-gradient(180deg,#f4f4f4 0%,#c9cacb 40%,#b1b3b6 70%,#e9e9e9 100%);border-radius:4px}
.hero-dots{left:520px;top:622px;display:flex;gap:8px}
.hero-dots i{width:14px;height:14px;border-radius:50%;background:#cfcfcf;border:1px solid #bbb}

.thumbs{left:111px;top:652px;display:flex;gap:20px}
.thumb{width:143px;height:134px;border-bottom:6px solid var(--link-blue)}
.thumb:nth-child(1){background:linear-gradient(135deg,#e8e8e8,#8a8a8a)}
.thumb:nth-child(2){background:linear-gradient(135deg,#1b3f8a,#5a86cf)}
.thumb:nth-child(3){background:linear-gradient(135deg,#c6c6c6,#545454)}
.thumb:nth-child(4){background:linear-gradient(135deg,#d8d8d8,#8f8f8f)}
.thumb:nth-child(5){background:linear-gradient(135deg,#bcbcbc,#333)}
.thumb:nth-child(6){background:linear-gradient(135deg,#e0e0e0,#3b3b3b)}

.panel{border:2px solid var(--line);border-radius:4px;background:#fff}
.panel-title{font-size:20px;font-weight:600;color:var(--ink)}

.product-info{left:115px;top:815px;width:658px;height:726px;padding:28px 22px 28px 30px}
.product-info h3{font-size:16px;font-weight:600;margin:38px 0 10px 8px;padding-bottom:6px;border-bottom:1px solid var(--soft-line);width:340px}
.product-info .desc{font-size:15px;line-height:21px;color:#333;margin-left:8px;text-align:justify}
.features{list-style:none;margin:16px 0 0 36px;font-size:20px;line-height:35.5px;color:#333}

.reviews{left:115px;top:1548px;width:658px;height:330px;padding:14px 26px}
.review-head{display:flex;justify-content:space-between;align-items:center;margin-top:12px}
.review-head h4{font-size:20px;font-weight:500;color:var(--price-red)}
.reviewer{display:flex;align-items:center;gap:10px;font-size:17px;color:#444;margin-top:-8px}
.avatar{width:48px;height:48px;border-radius:50%;background:linear-gradient(135deg,#9a9a9a,#3a3a3a)}
.review-body{font-size:15px;line-height:21px;color:#333;margin-top:4px;text-align:justify}
.rating-bar{margin-top:16px;height:64px;background:var(--rating-bg);display:flex;align-items:center;padding:0 18px;font-family:Roboto,sans-serif}
.rating-bar .supporters{margin-left:128px;font-size:14px;font-weight:500;display:flex;align-items:center;gap:8px}
.rating-bar .share{margin-left:auto}
.more{position:absolute;right:42px;bottom:12px;font-size:15px;color:var(--price-red)}

.warranty{left:115px;top:1888px;width:658px;height:343px;padding:16px 26px;font-family:Roboto,sans-serif}
.warranty .panel-title{font-family:"Fira Sans",sans-serif}
.warranty h4{font-size:17px;font-weight:700;color:var(--link-blue);margin-top:24px}
.faq{list-style:none;margin-top:6px}
.faq li{font-size:16px;font-weight:700;color:#222;display:flex;gap:10px;align-items:center;margin-bottom:1px}
.faq li .dot{width:15px;height:15px;flex:none}
.faq p{font-weight:400;font-size:16px;line-height:21px;margin:2px 0 14px 30px;color:#333;text-align:justify}

.shipping{left:115px;top:2241px;width:658px;height:216px;padding:14px 26px}
.shipping p{font-size:15px;line-height:21px;color:#333;margin-top:18px;text-align:justify}

.buy-box{left:796px;top:815px;width:278px;height:477px;padding:16px 14px;font-family:Roboto,sans-serif}
.buy-box .price{font-family:"Oswald",sans-serif;font-size:30px;font-weight:500;color:var(--price-red)}
.spec{display:grid;grid-template-columns:128px 1fr;font-size:14.5px;row-gap:11px;margin:18px 0 0 10px;color:#333}
.spec .strike{text-decoration:line-through}
.req{color:var(--price-red)}
.color-label{font-size:15px;font-weight:700;margin:10px 0 0 0}
.select{height:44px;border:1px solid #aaa;border-radius:3px;margin-top:12px;display:flex;align-items:center;justify-content:space-between;padding:0 16px 0 26px;font-size:18px;color:#333}
.caret{width:0;height:0;border-left:8px solid transparent;border-right:8px solid transparent;border-top:8px solid #888}
.required{font-size:15px;margin-top:18px}
.qty{display:flex;align-items:center;margin-top:18px;font-size:15px;color:var(--accent-orange)}
.qty .qty-select{margin-left:40px;width:108px;height:30px;border:1px solid #aaa;border-radius:2px;display:flex;align-items:center;justify-content:space-between;padding:0 10px;color:#333;font-size:16px}
.add-cart{margin-top:16px;height:42px;background:var(--accent-orange);color:#fff;font-weight:700;font-size:17px;text-align:center;line-height:42px;border-radius:3px}
.free-ship{margin:20px auto 0;width:188px;height:34px;background:var(--brand-blue);color:#fff;font-style:italic;font-weight:700;font-size:16px;line-height:34px;text-align:center;clip-path:polygon(0 0,100% 0,94% 50%,100% 100%,0 100%)}

.side-head{background:var(--brand-blue);color:#fff;font-family:Roboto,sans-serif;font-weight:500;font-size:16px;height:47px;line-height:47px;padding-left:16px}
.fpt{left:796px;top:1315px;width:278px}
.fpt-item{border:2px solid var(--line);border-top:none;height:116px;display:flex;padding:10px 12px;font-family:Roboto,sans-serif}
.fpt-item + .fpt-item{margin-top:8px;border-top:2px solid var(--line)}
.fpt-img{width:56px;height:90px;background:linear-gradient(180deg,#777,#222);border-radius:3px;flex:none}
.fpt-text{margin-left:24px;padding-top:10px}
.fpt-text h5{font-size:15px;font-weight:700;color:var(--link-blue);line-height:17px}
.fpt-text small{display:block;font-size:13px;color:#333;line-height:16px;margin-top:2px}
.fpt-text .free{color:var(--price-red);font-weight:700;font-size:14px;margin-left:32px}
.fpt-text .p{font-family:"Oswald",sans-serif;font-size:26px;font-weight:500;color:var(--price-red);display:flex;align-items:center;gap:10px;margin-top:2px}
.chk{width:15px;height:15px;border:1px solid #aaa;background:#f4f4f4}

.indoor{left:796px;top:1884px;width:278px;height:298px;border:2px solid var(--line);border-top:none}
.indoor-photo{margin:16px auto 0;width:160px;height:92px;background:linear-gradient(180deg,#5aa0e6,#1e5fb8 60%,#9a9a9a)}
.indoor h5{font-family:Roboto,sans-serif;font-size:16px;font-weight:500;color:var(--link-blue);margin:24px 0 0 44px;line-height:22px}
.indoor .old{font-family:"Oswald",sans-serif;font-size:20px;margin:4px 0 0 38px;text-decoration:line-through}
.indoor .new{font-family:"Oswald",sans-serif;font-size:26px;color:var(--price-red);margin-left:44px;line-height:28px}

.signup{left:178px;top:2535px;font-family:Roboto,sans-serif}
.signup h2{font-size:25px;font-weight:700;color:#111}
.signup .lead{display:flex;gap:6px;font-size:15.5px;line-height:19px;color:#333;margin-top:8px;margin-left:-30px}
.signup .quote{font-family:Georgia,serif;font-size:42px;color:#bbb;line-height:30px;width:24px}
.signup .fields{margin-top:22px;font-size:15.5px;color:#222;margin-left:-2px}
.signup .row{display:flex;align-items:center;gap:8px;margin-bottom:8px}
.signup .input{height:22px;width:146px;background:#e2e2e2;border:1px solid #bbb}
.signup .input.wide{width:254px}
.signup .btn{margin-top:16px;width:246px;height:46px;background:var(--accent-orange);color:#fff;font-size:18px;text-align:center;line-height:46px;border-radius:3px;box-shadow:0 2px 2px #c97448}

.footer-scene{left:0;top:2735px;width:1200px;height:82px;background:linear-gradient(180deg,#ffffff 0%,#d3deea 40%,#7f9ab8 100%)}
</style>
</head>
<body>

<header class="page-header abs"><h1>up to 16’8” Long and 90” Wide</h1></header>

<nav class="breadcrumb abs"><span>Home &gt;</span><span>Boat Covers &gt;</span><span>Center Console with Bow Rails &gt;</span><span class="current">up to 16’8” Long and 90” Wide</span></nav>

<div class="product-frame abs"></div>

<div class="fits-bar abs">Fits : Center Console with Bow Rails upto 16’8” Long and 90” Wide</div>

<div class="hero-photo abs" role="img" aria-label="Grey boat cover strapped over a center console boat on a trailer"></div>
<div class="hero-dots abs"><i></i><i></i><i></i><i></i><i></i><i></i></div>

<div class="thumbs abs">
  <div class="thumb" role="img" aria-label="Five star fit badge"></div>
  <div class="thumb" role="img" aria-label="Fabric layers diagram"></div>
  <div class="thumb" role="img" aria-label="Buckle strap detail"></div>
  <div class="thumb" role="img" aria-label="Elastic hem cord detail"></div>
  <div class="thumb" role="img" aria-label="Strap close-up"></div>
  <div class="thumb" role="img" aria-label="Straps and storage bag"></div>
</div>

<section class="product-info panel abs">
  <h2 class="panel-title">Product Info</h2>
  <h3>Description :</h3>
  <p class="desc">When a Boat is stored outside it is exposed to harmful elements such as wind, dirt, rian, and UV. The Tidecrest Supreme is the most powerful cover available providing 10x more strength and protection compared to the competition. The 1200 denier fabric is 100% waterproof and provides excellent protection against sun, rain, wind and snow.</p>
  <h3>Features :</h3>
  <ul class="features">
    <li>5 Star Fit. FIt guaranteed or your money back</li>
    <li>10 Year Warranty. Full warranty covering rips and tears</li>
    <li>The covers comes in Grey, Blue and Maroon</li>
    <li>The Fabric is pure 100% Marine Polyster (No. Cotton mix)</li>
    <li>No worries, the cover is 100% waterproof</li>
    <li>Fully Breathable, you'll never see mold or mildew</li>
    <li>UV resistant an dalso prevents heat buildup</li>
    <li>Fully Trailerable (straps included)</li>
    <li>The Cover also comes with an integrated hen cord to<br>be used when mooring or on boat lifts</li>
    <li>Tough - Strong - Durable</li>
  </ul>
</section>

<section class="reviews panel abs">
  <h2 class="panel-title">Reviews</h2>
  <div class="review-head">
    <h4>Nunc vestibulum sodales nulla</h4>
    <div class="reviewer">Dana Reyes <span class="avatar" role="img" aria-label="Reviewer avatar"></span></div>
  </div>
  <p class="review-body">Lorem ipsum dolor sit amet, consectetur adipisicing elit, sed do eiusmod tempor incididunt ut labore et dolore magna aliqua. Ut enim ad minim veniam, quis nostrud exercitation ullamco laboris nisi ut aliquip ex ea commodo consequat. Duis aute irure dolor in reprehenderit in voluptate velit esse cillum dolore eu fugiat nulla pariatur.</p>
  <div class="rating-bar">
    <svg width="136" height="26" viewBox="0 0 136 26">
      <defs><path id="star" d="M13 1l3.6 7.6 8.3 1-6.1 5.8 1.6 8.2L13 19.6 5.6 23.6l1.6-8.2L1.1 9.6l8.3-1z"/>
      <clipPath id="half"><rect x="0" y="0" width="13" height="26"/></clipPath></defs>
      <g fill="#0a3a7a"><use href="#star"/><use href="#star" x="27"/><use href="#star" x="54"/><use href="#star" x="81"/></g>
      <use href="#star" x="108" fill="none" stroke="#0a3a7a" stroke-width="1.6"/>
      <g transform="translate(108 0)" clip-path="url(#half)"><use href="#star" fill="#0a3a7a"/></g>
    </svg>
    <span class="supporters">
      <svg width="24" height="18" viewBox="0 0 24 18" fill="#1f4fbf"><circle cx="12" cy="5" r="4"/><circle cx="4.5" cy="6" r="3"/><circle cx="19.5" cy="6" r="3"/><path d="M5 18c0-5 3-8 7-8s7 3 7 8z"/><path d="M0 16c0-4 2-6 4.5-6 1 0 2 .3 2.6 1-1.3 1.4-2 3-2.1 5z"/><path d="M24 16c0-4-2-6-4.5-6-1 0-2 .3-2.6 1 1.3 1.4 2 3 2.1 5z"/></svg>
      15,583 Supporters
    </span>
    <svg class="share" width="16" height="16" viewBox="0 0 16 16" fill="#333"><circle cx="12.5" cy="3" r="2.5"/><circle cx="3" cy="8" r="2.5"/><circle cx="12.5" cy="13" r="2.5"/><path d="M3 8l9.5-5M3 8l9.5 5" stroke="#333" stroke-width="1.4"/></svg>
  </div>
  <a class="more">more...</a>
</section>

<section class="warranty panel abs">
  <h2 class="panel-title">Warranty</h2>
  <h4>LIMITED WARRANTY POLICY AND GUIDELINES</h4>
  <ul class="faq">
    <li><svg class="dot" viewBox="0 0 16 16"><circle cx="8" cy="8" r="8" fill="#e02020"/><rect x="3.5" y="6.8" width="9" height="2.4" fill="#fff"/></svg>WHAT IS THE SUMMIT RIDGE® WARRANTY POLICY?</li>
    <p>Lorem ipsum dolor sit amet, consectetur adipisicing elit, sed do eiusmod tempor incididunt ut labore et dolore magna aliqua. Ut enim ad minim veniam, quis nostrud exercitation ullamco laboris nisi ut aliquip ex ea commodo consequat. Duis aute irure dolor in reprehenderit in voluptate velit esse cillum dolore eu fugiat nulla pariatur.</p>
    <li><svg class="dot" viewBox="0 0 16 16"><circle cx="8" cy="8" r="8" fill="#111"/><path d="M3.5 8h9M8 3.5v9" stroke="#fff" stroke-width="2.4"/></svg>WHAT DOES "LIFETIME" MEAN?</li>
    <li><svg class="dot" viewBox="0 0 16 16"><circle cx="8" cy="8" r="8" fill="#111"/><path d="M3.5 8h9M8 3.5v9" stroke="#fff" stroke-width="2.4"/></svg>IS NORMAL WEAR AND TEAR COVERED BY WARRANTY?</li>
    <li><svg class="dot" viewBox="0 0 16 16"><circle cx="8" cy="8" r="8" fill="#111"/><path d="M3.5 8h9M8 3.5v9" stroke="#fff" stroke-width="2.4"/></svg>HOW TO SEND MY PRODUCT IN FOR A WARRANTY CLAIM?</li>
  </ul>
</section>

<section class="shipping panel abs">
  <h2 class="panel-title">Shipping</h2>
  <p>Lorem ipsum dolor sit amet, consectetur adipisicing elit, sed do eiusmod tempor incididunt ut labore et dolore magna aliqua. Ut enim ad minim veniam, quis nostrud exercitation ullamco laboris nisi ut aliquip ex ea commodo consequat. Duis aute irure dolor in reprehenderit in voluptate velit esse cillum dolore eu fugiat nulla pariatur.</p>
  <a class="more">more...</a>
</section>

<aside class="buy-box panel abs">
  <div class="price">$331.50</div>
  <div class="spec">
    <span>Regular Price :</span><span class="strike">$ 442.00</span>
    <span>Your Save :</span><span>$110.50</span>
    <span>Availability :</span><span>Ready to ship</span>
    <span>Ships :</span><span>1 Business Day</span>
  </div>
  <div class="color-label"><span class="req">*</span> Color</div>
  <div class="select">Please Select <span class="caret"></span></div>
  <div class="required req">* Required Fields</div>
  <div class="qty">Quantity : <span class="qty-select">1 <span class="caret"></span></span></div>
  <div class="add-cart">ADD TO CART</div>
  <div class="free-ship">Free Shipping*</div>
</aside>

<aside class="fpt abs">
  <div class="side-head">Frequently Purchased Together</div>
  <div class="fpt-item">
    <div class="fpt-img" role="img" aria-label="Support pole"></div>
    <div class="fpt-text"><h5>SUPPORT POLE</h5><small>Works for Boats and Trucks</small><div class="p">$30.75 <span class="chk"></span></div></div>
  </div>
  <div class="fpt-item">
    <div class="fpt-img" role="img" aria-label="Boat motor cover" style="background:linear-gradient(180deg,#2b5fb8,#0d2f74)"></div>
    <div class="fpt-text"><h5>BOAT MOTOR COVER</h5><small>Heavy duty waterproof material</small><div class="p">$30.75 <span class="chk"></span></div></div>
  </div>
  <div class="fpt-item">
    <div class="fpt-img" role="img" aria-label="Strap and buckle pack"></div>
    <div class="fpt-text"><h5>132 IN. STRAPS AND BUCKLE PACK</h5><span class="free">FREE !</span><div class="p">$30.75 <span class="chk"></span></div></div>
  </div>
  <div class="fpt-item">
    <div class="fpt-img" role="img" aria-label="Storage bag"></div>
    <div class="fpt-text"><h5>STORAGE BAG</h5><span class="free">FREE !</span><div class="p">$30.75 <span class="chk"></span></div></div>
  </div>
</aside>

<aside class="indoor abs">
  <div class="side-head">Looking for and indoor Cover ?</div>
  <div class="indoor-photo" role="img" aria-label="Blue indoor boat cover on a trailer"></div>
  <h5>Bramble 600 denier Boat<br>Cover fits V-Hull Runabou</h5>
  <div class="old">$ 300.00</div>
  <div class="new">$ 138.81</div>
</aside>

<section class="signup abs">
  <h2>SIGN ME UP !</h2>
  <div class="lead"><span class="quote">“</span><span>I would like to receive your ebook in my inbox<br>on a regular basis</span></div>
  <div class="fields">
    <div class="row">First Name <span class="input"></span> <span>last name</span> <span class="input"></span></div>
    <div class="row">email address : <span class="input wide"></span></div>
  </div>
  <div class="btn">SUBSCRIBE</div>
</section>

<div class="footer-scene abs" role="img" aria-label="Soft blue mountain range at the foot of the page"></div>

</body>
</html>
```